LIFE CHANGING NEW WEBSITE DESIGN NEEDED FOR FULL WEBSITE- FUN/FEMININE!

I need a website designed for a personal financial advice website geared at women called BLUE OTTER LANTERN. I will be providing free financial advice around topics of making, saving, spending and sharing money. The concept is to change the way women understand money and the necessity around building various passive income streams to ensure full financial freedom. This will then carry down to advice for mothers with children and children in particular. The website should be elegant and yet witty. I don't want lots of serious photos but more relatable. I will have a photo of myself and my story as this is a blog and needs to be relatable to women and mothers. I like pinks and greys. I want to have a pink piggy bank being broken with a hammer in the front screen to break our traditional mindset around piggy bank saving/spending habits. I have created a logo that is a pink piggy head with BLUE OTTER LANTERN that needs to be incorporated so that it blends into the heading. I have also already started designing the website on Squarespace and can provide access to that. Basically it should have a format of BLUE OTTER LANTERN LOGO center in header then on left hand navigation: MAKE, SAVE, SPEND, SHARE then on right hand header navigation: MISSION, GET STARTED, CONTACT BOL I would like to have the front page when you go to the url to have the image of the piggy bank being broken then a catchy phrase then under 4 boxes with MAKE (image and description) SAVE (image and description) SPEND (image and description) SHARE (image and description) if you click on those or the title they go to pages that are dedicated to each them. Each page should have a little intro on the topic then I want lots of blog links as I will be mainly writing blogs. Each blog site should have ability to write comments as well. I need social media icons on each page too. Please let me know what you need from me to get started. I prefer having a discussion if possible to not waste anyone's time. I need the site to be easy for me to use and add blogs/urls etc as needed. I also need the site to be put into my domain that I already purchased: www.blueotterlantern-sample.com

Target Market(s)

teenage girls, 20 something girls, 30 something girls and mothers

Coding

Coded - Design and coding required

Number of Pages Required

5+ page

Font styles to use
Sans Serif

Colors
e667a6
e34197
f59195
eea4c8
aaaaaa
cbcbcb
959595

Requirements
Must have
• TOP NAVIGATION
• MAKE SAVE SPEND SHARE LOGO/BLUE OTTER LANTERN MISSION GET STARTED CONTACT BOL
• FRONT PAGE: IMAGE OF PIGGY BANK BEING BROKEN WITH A HAMMER
• CATCH PHRASE OVER THE IMAGE
• BUTTON IN PINK- TAKE ACTION (WHICH DIRECTS TO TAKE ACTION TAB ON NAVIGATION HEADER
• 4 BOXES BELOW MAIN IMAGE WITH IMAGE/DESCRIPTIONS FOR MAKE, SAVE, SPEND, SHARE THAT EACH GO TO THE PAGES FROM THE NAVIGATION HEADER
• EACH PAGE SHOULD BE DEDICATED TO THOSE TOPICS THEN THERE IS AN INTRO ON EACH PAGE THEN THE LINKS TO DIFFERENT BLOGS AROUND EACH TOPIC FOR MAKE, SAVE, SPEND, SHARE
• EACH BLOG SHOULD HAVE COMMENTS SECTION AND SOCIAL MEDIA ICONS
• (GOOD TO USE PINKS/GREYS)
Should not have
• BE SUPER BUSY, CLUTTERED, FEEL LIKE I AM SELLING SOMETHING

```html
<!DOCTYPE html>
<html lang="en">
<head>
<meta charset="utf-8">
<title>Blue Otter Lantern</title>
<link href="https://fonts.googleapis.com/css2?family=Lato:wght@400;700;900&display=swap" rel="stylesheet">
<style>
:root{
  --magenta:#d4106f;
  --pink:#e667a6;
  --coral:#f27b84;
  --soft:#eea4c8;
  --grey-card:#f1f1f1;
  --grey-line:#cbcbcb;
  --text:#3a3a3a;
  --muted:#555;
  --dark:#2a2a2a;
  --white:#fff;
}
*{box-sizing:border-box;margin:0;padding:0}
html,body{width:1200px;height:2809px;overflow:hidden}
body{font-family:'Lato',sans-serif;color:var(--text);background:var(--white);position:relative}
.abs{position:absolute}
/* header */
.site-header{position:absolute;top:0;left:0;width:1200px;height:133px;background:var(--white)}
.nav a{position:absolute;top:60px;font-size:14px;font-weight:700;color:#333;text-decoration:none;letter-spacing:.2px}
.brand{position:absolute;left:450px;top:32px;width:300px;text-align:center}
.brand .dot{display:block;width:38px;height:38px;border:3px solid var(--pink);border-radius:50%;margin:0 auto 4px}
.brand span{font-size:20px;font-weight:700;color:var(--pink)}
/* hero */
.hero{position:absolute;top:133px;left:0;width:1200px;height:590px;background:linear-gradient(100deg,#c0001c 0%,#d2102c 45%,#b00018 100%)}
.hero-photo{position:absolute;right:0;top:0;width:560px;height:590px;background:radial-gradient(ellipse at 60% 45%,#e5333d 0%,#b8001b 70%)}
.hero h1{position:absolute;left:74px;top:170px;font-size:58px;font-weight:900;color:var(--white);letter-spacing:-.5px}
.hero p{position:absolute;left:76px;top:245px;width:560px;font-size:22px;line-height:32px;color:var(--white);font-weight:700}
.btn{display:block;text-align:center;background:var(--magenta);color:var(--white);font-weight:700;font-size:18px;border-radius:24px;text-decoration:none}
.hero .btn{position:absolute;left:76px;top:333px;width:208px;height:47px;line-height:47px}
/* topic cards */
.topic{position:absolute;top:792px;width:241px;height:484px;background:var(--grey-card);border-radius:120px 120px 40px 40px;text-align:center}
.topic .photo{width:208px;height:208px;border-radius:50%;margin:16px auto 0;border-bottom:4px solid var(--magenta);background:linear-gradient(160deg,#d9d2cc,#7c6f68)}
.topic h3{margin-top:26px;font-size:22px;font-weight:900;color:var(--magenta)}
.topic p{margin:10px 16px 0;font-size:14.5px;line-height:26px;color:var(--muted)}
/* welcome band */
.welcome{position:absolute;top:1330px;left:0;width:1200px;height:560px;background:var(--coral);text-align:center;color:var(--white)}
.welcome h2{margin-top:116px;font-size:28px;font-weight:900}
.welcome p{width:1060px;margin:16px auto 0;font-size:16.5px;line-height:28px}
.welcome p+p{margin-top:16px}
.welcome .btn{width:208px;height:47px;line-height:47px;margin:42px auto 0}
/* blog */
.blog-title{position:absolute;top:1962px;left:0;width:1200px;text-align:center;font-size:28px;font-weight:900;color:#333}
.post{position:absolute;top:2032px;width:331px}
.post .photo{height:188px}
.tag{display:inline-block;margin-top:24px;background:var(--pink);color:var(--white);font-size:12px;font-weight:700;padding:7px 11px}
.post h4{margin-top:12px;font-size:20px;line-height:25px;font-weight:700;color:#333}
.date{margin-top:6px;font-size:12px;font-weight:700;color:var(--magenta);padding-left:32px;position:relative}
.date:before{content:"";position:absolute;left:0;top:2px;width:10px;height:10px;background:var(--magenta);border-radius:2px}
.post p{margin-top:8px;font-size:14px;line-height:24px;color:var(--muted)}
.comment{margin-top:12px;height:39px;border:1px solid var(--grey-line);font-size:12px;color:#777;padding:12px}
.socials{margin-top:18px;display:flex;gap:14px}
.socials i{width:12px;height:12px;border-radius:50%;background:#666;display:block}
/* footer */
.site-footer{position:absolute;top:2588px;left:0;width:1200px;height:221px;background:var(--dark);color:var(--white)}
.site-footer .brand{left:75px;top:45px;width:auto;text-align:left}
.site-footer .brand .dot{margin:0 0 4px 70px;width:32px;height:32px}
.site-footer .brand span{font-size:18px;color:var(--pink)}
.copy{position:absolute;left:75px;top:128px;font-size:13px;line-height:21px}
.f-head{position:absolute;top:42px;font-size:15px;font-weight:700}
.f-links{position:absolute;top:72px;font-size:15px;line-height:29px;list-style:none}
.f-input{position:absolute;left:625px;top:77px;width:243px;height:38px;border:1px solid var(--white);font-size:13px;padding:11px 14px}
.f-btn{position:absolute;left:625px;top:128px;width:77px;height:38px;line-height:38px;background:var(--coral);font-size:13px;font-weight:700;text-align:center}
.f-social{position:absolute;left:925px;top:76px;display:flex;gap:18px}
.f-social i{display:block;width:20px;height:20px;border-radius:50%;background:#ddd}
</style>
</head>
<body>

<header class="site-header">
  <nav class="nav">
    <a href="#" style="left:74px">MAKE</a>
    <a href="#" style="left:158px">SAVE</a>
    <a href="#" style="left:235px">SPEND</a>
    <a href="#" style="left:324px">SHARE</a>
    <a href="#" style="left:784px">MISSION</a>
    <a href="#" style="left:886px">GET STARTED</a>
    <a href="#" style="left:1021px">CONTACT BOL</a>
  </nav>
  <div class="brand"><i class="dot"></i><span>Blue Otter Lantern</span></div>
</header>

<section class="hero">
  <div class="hero-photo" role="img" aria-label="Woman in red holding a hammer over a white piggy bank"></div>
  <h1>BLUE OTTER LANTERN.</h1>
  <p>Get a free financial advice around topics of making, saving, spending and sharing money..</p>
  <a class="btn" href="#">TAKE ACTION</a>
</section>
<svg class="abs" style="left:0;top:680px" width="1200" height="60" viewBox="0 0 1200 60" preserveAspectRatio="none">
  <path d="M0 0 L1200 0 L1200 13 C1000 28 850 50 600 40 C400 32 200 8 0 18 Z" fill="#bf0a22"/>
</svg>

<article class="topic" style="left:75px">
  <div class="photo" role="img" aria-label="Woman at laptop with money flying out"></div>
  <h3>MAKE</h3>
  <p>Lorem ipsum dolor sit amet, consectetur adipiscing elit. Duis ultrices odio sit amet ex ultricies euismoded id varius lectus. Etiam id tortor semper, viverra metus et</p>
</article>
<article class="topic" style="left:345px">
  <div class="photo" role="img" aria-label="Mother and daughter with a pink piggy bank"></div>
  <h3>SAVE</h3>
  <p>Lorem ipsum dolor sit amet, consectetur adipiscing elit. Duis ultrices odio sit amet ex ultricies euismoded id varius lectus. Etiam id tortor semper, viverra metus et</p>
</article>
<article class="topic" style="left:615px">
  <div class="photo" role="img" aria-label="Woman holding a fan of banknotes before a chalkboard of doodles"></div>
  <h3>SPEND</h3>
  <p>Lorem ipsum dolor sit amet, consectetur adipiscing elit. Duis ultrices odio sit amet ex ultricies euismoded id varius lectus. Etiam id tortor semper, viverra metus et</p>
</article>
<article class="topic" style="left:885px">
  <div class="photo" role="img" aria-label="Businesswoman advising a client at a desk"></div>
  <h3>SHARE</h3>
  <p>Lorem ipsum dolor sit amet, consectetur adipiscing elit. Duis ultrices odio sit amet ex ultricies euismoded id varius lectus. Etiam id tortor semper, viverra metus et</p>
</article>

<section class="welcome">
  <h2>WELCOME TO BLUE OTTER LANTERN (BOL)!</h2>
  <p>My mission is simple- I want to challenge you to rethink the way you think about growing, spending and saving money. By redesigning your life around your finances I want you to run your life as if you are the CEO of your own business, and the business is maximising the value and profitability of your life.</p>
  <p>It is shocking that in today's world of information we are we still live in a society where most educated people leave school without even a basic understanding of money and how to run their lives outside of a just obtaining a job. Instead, we are taught to work hard in school, find a good job, get married, have children, save up for big expenses (like homes, school tuition..) then retire. By completely lacking personal finance education in schools and few resources to help, it is little wonder that life often feels like one big rat race of no end.</p>
  <a class="btn" href="#">READ MORE</a>
</section>
<svg class="abs" style="left:0;top:1325px" width="1200" height="50" viewBox="0 0 1200 50" preserveAspectRatio="none">
  <path d="M0 0 L1200 0 L1200 8 C1000 22 850 20 650 16 C450 12 300 46 0 20 Z" fill="#fff"/>
  <path d="M560 15 C800 10 950 32 1200 6" stroke="#d4106f" stroke-width="5" fill="none"/>
</svg>
<svg class="abs" style="left:0;top:1870px" width="1200" height="45" viewBox="0 0 1200 45" preserveAspectRatio="none">
  <path d="M0 15 C250 38 450 2 600 5 C800 8 1000 30 1200 8 L1200 45 L0 45 Z" fill="#fff"/>
  <path d="M0 14 C200 30 450 14 580 4" stroke="#d4106f" stroke-width="5" fill="none"/>
</svg>

<h2 class="blog-title">BLOG POSTS</h2>

<article class="post" style="left:75px">
  <div class="photo" role="img" aria-label="Two businesswomen discussing documents at a table" style="background:linear-gradient(120deg,#e7e9ec,#8a8f98)"></div>
  <span class="tag">MAKE</span>
  <h4>ALIQUAM CONSEQUAT IN DUI VEL CONDIMENTUM</h4>
  <div class="date">JUN 20, 2019</div>
  <p>Nunc ante sapien, scelerisque eget velit eu, placerat molestie ligula. Vestibulum ante ipsum primis in faucibus orci luctus et ultrices posuere..</p>
  <div class="comment">Enter comment..</div>
  <div class="socials"><i></i><i></i><i></i><i></i><i></i></div>
</article>
<article class="post" style="left:435px">
  <div class="photo" role="img" aria-label="Person in white shirt holding banknotes on yellow background" style="background:linear-gradient(120deg,#f3e20e,#d4b800 60%,#8a7a10)"></div>
  <span class="tag">SPEND</span>
  <h4>ALIQUAM CONSEQUAT IN DUI VEL CONDIMENTUM</h4>
  <div class="date">JUN 20, 2019</div>
  <p>Nunc ante sapien, scelerisque eget velit eu, placerat molestie ligula. Vestibulum ante ipsum primis in faucibus orci luctus et ultrices posuere..</p>
  <div class="comment">Enter comment..</div>
  <div class="socials"><i></i><i></i><i></i><i></i><i></i></div>
</article>
<article class="post" style="left:796px">
  <div class="photo" role="img" aria-label="Smiling woman in yellow with a white piggy bank" style="background:linear-gradient(120deg,#c89a5a,#f0c040 50%,#e8ede0)"></div>
  <span class="tag">SAVE</span>
  <h4>ALIQUAM CONSEQUAT IN DUI VEL CONDIMENTUM</h4>
  <div class="date">JUN 20, 2019</div>
  <p>Nunc ante sapien, scelerisque eget velit eu, placerat molestie ligula. Vestibulum ante ipsum primis in faucibus orci luctus et ultrices posuere..</p>
  <div class="comment">Enter comment..</div>
  <div class="socials"><i></i><i></i><i></i><i></i><i></i></div>
</article>

<footer class="site-footer">
  <div class="brand"><i class="dot"></i><span>Blue Otter Lantern</span></div>
  <p class="copy">Copyright © 2019. Company Name.<br>All Right Reserved</p>
  <div class="f-head" style="left:346px">SITE MAP</div>
  <ul class="f-links" style="left:346px;top:66px"><li>Make</li><li>Save</li><li>Spend</li><li>Share</li></ul>
  <ul class="f-links" style="left:462px;top:69px"><li>Mission</li><li>Get Started</li><li>Contact Bol</li></ul>
  <div class="f-head" style="left:625px">EMAIL SIGN UP</div>
  <div class="f-input">Enter Email Address</div>
  <div class="f-btn">SIGN UP</div>
  <div class="f-head" style="left:925px">FOLLOW US</div>
  <div class="f-social"><i></i><i></i><i></i><i></i><i></i></div>
</footer>

</body>
</html>
```